Heron Loan Partners Business Card

We need a business card design for our mortgage servicing company. In addition to servicing the loans of homeowners, we help homeowners with purchasing their homes and any mortgage refinancing. We would like to see designs that use the colors in the logo attached below (gold-ish yellow and navy blue), and any other design you deem fit! The design should communicate a simpler life with smart mortgages provided by Heron.

```html
<!DOCTYPE html>
<html lang="en">
<head>
<meta charset="utf-8">
<title>Heron Loan Partners – Business Card</title>
<link rel="stylesheet" href="https://fonts.googleapis.com/css2?family=Open+Sans:wght@400;600;700&display=swap">
<style>
  :root {
    --navy: #251f52;
    --gold: #e1b03c;
    --white: #ffffff;
    --backdrop: #222222;
  }
  * { box-sizing: border-box; margin: 0; padding: 0; }
  html, body { width: 1200px; height: 780px; overflow: hidden; }
  body {
    background: var(--backdrop);
    font-family: "Open Sans", Arial, sans-serif;
    position: relative;
  }
  .card {
    position: absolute;
    top: 235px;
    width: 540px;
    height: 310px;
    border-radius: 22px;
    background: var(--white);
    border: 3px solid var(--gold);
    overflow: hidden;
  }
  .card--front { left: 40px; }
  .card--back { left: 620px; }

  .wordmark {
    font-weight: 700;
    color: var(--gold);
    letter-spacing: 0.5px;
    white-space: nowrap;
  }
  .card--front .wordmark {
    position: absolute;
    left: 0; right: 0; top: 128px;
    text-align: center;
    font-size: 38px;
  }
  .card--back .wordmark {
    position: absolute;
    right: 34px; top: 28px;
    font-size: 24px;
  }

  .wave { position: absolute; inset: 0; width: 100%; height: 100%; }

  .contact {
    position: absolute;
    left: 30px; top: 160px;
    color: var(--white);
  }
  .contact__name {
    color: var(--gold);
    font-weight: 700;
    font-size: 20px;
    line-height: 24px;
  }
  .contact__role {
    font-weight: 600;
    font-size: 13px;
    line-height: 18px;
    margin-bottom: 8px;
  }
  .contact__address {
    font-size: 12px;
    line-height: 16px;
    margin-bottom: 8px;
  }
  .contact__list { list-style: none; font-size: 12px; line-height: 17px; }
  .contact__list li { display: flex; align-items: center; gap: 8px; }
  .contact__icon { width: 12px; height: 12px; flex: none; }
</style>
</head>
<body>

<section class="card card--front" aria-label="Card front">
  <div class="wordmark">Heron Loan Partners</div>
</section>

<section class="card card--back" aria-label="Card back">
  <svg class="wave" viewBox="0 0 540 310" preserveAspectRatio="none" aria-hidden="true">
    <path fill="var(--navy)" d="M0,110 C160,80 360,100 540,28 L540,46 C360,112 160,90 0,118 Z"/>
    <path fill="var(--gold)" d="M0,126 C150,96 380,120 540,58 L540,76 C380,136 150,112 0,142 Z"/>
    <path fill="var(--navy)" d="M0,150 C150,120 380,146 540,86 L540,310 L0,310 Z"/>
  </svg>

  <div class="wordmark">Heron Loan Partners</div>

  <div class="contact">
    <p class="contact__name">Lena Marsh</p>
    <p class="contact__role">Co-Founder</p>
    <p class="contact__address">418 Alder Way, Suite 120<br>Brookfield, TX 75010</p>
    <ul class="contact__list">
      <li>
        <svg class="contact__icon" viewBox="0 0 24 24" aria-hidden="true"><path fill="var(--gold)" d="M6.6 10.8a15.2 15.2 0 0 0 6.6 6.6l2.2-2.2a1 1 0 0 1 1-.25 11.4 11.4 0 0 0 3.6.57 1 1 0 0 1 1 1V20a1 1 0 0 1-1 1A17 17 0 0 1 3 4a1 1 0 0 1 1-1h3.5a1 1 0 0 1 1 1c0 1.25.2 2.45.57 3.57a1 1 0 0 1-.25 1Z"/></svg>
        (555) 214-3087
      </li>
      <li>
        <svg class="contact__icon" viewBox="0 0 24 24" aria-hidden="true"><path fill="var(--gold)" d="M2 5h20v14H2Zm2 2v.5l8 5 8-5V7Z"/></svg>
        info@heronloans.com
      </li>
      <li>
        <svg class="contact__icon" viewBox="0 0 24 24" aria-hidden="true"><circle cx="12" cy="12" r="10" fill="none" stroke="var(--gold)" stroke-width="2.4"/><path d="M2 12h20M12 2c3 3 3 17 0 20M12 2c-3 3-3 17 0 20" fill="none" stroke="var(--gold)" stroke-width="1.8"/></svg>
        www.heronloans.com
      </li>
    </ul>
  </div>
</section>

</body>
</html>
```